Upgrade 4 Images - Bid 1, then we can discuss the other 3

We have a four graphics that we use in various presentations and business proposals. We want to upgrade them to make them really pop and match the level of service we provide, without going overboard.

We're open to new ideas, but the general form and content should stay the same.

I'd like to have all four designed by the same person, but I'm assuming this bid will be for 1 of the four, and then the other three can be contracted as additions.

```html
<!DOCTYPE html>
<html lang="en">
<head>
<meta charset="utf-8">
<title>Service Tiers</title>
<link rel="stylesheet" href="https://fonts.googleapis.com/css2?family=Source+Sans+3:wght@400;500&display=swap">
<style>
  :root {
    --orange: #ed7d31;
    --orange-dark: #b4561f;
    --ink: #58595b;
    --paper: #ffffff;
    --dash: #58595b;
  }
  html, body {
    margin: 0;
    padding: 0;
    width: 1200px;
    height: 479px;
    overflow: hidden;
    background: var(--paper);
  }
  .tier-diagram {
    display: block;
    width: 1200px;
    height: 479px;
    font-family: "Source Sans 3", "Myriad Pro", sans-serif;
  }
  .connector { stroke: var(--dash); stroke-width: 3; stroke-dasharray: 9 7; fill: none; }
  .frame { fill: none; stroke: var(--orange); stroke-width: 3.5; }
  .frame-inner { fill: var(--paper); stroke: var(--orange); stroke-width: 3.5; }
  .tab { fill: var(--orange); }
  .tab-fold { fill: var(--orange-dark); }
  .dot { fill: var(--orange); }
  .tier-title { fill: var(--paper); font-size: 38px; font-weight: 400; letter-spacing: 1.5px; }
  .tier-features { fill: var(--ink); font-size: 24px; font-weight: 400; text-anchor: middle; }
  .operator-ring { fill: var(--paper); stroke: var(--orange); stroke-width: 3.5; }
  .operator-disc { fill: var(--orange); }
  .operator-glyph { fill: var(--paper); }
</style>
</head>
<body>
<svg class="tier-diagram" viewBox="0 0 2560 1022" role="img" aria-label="Ad Hoc leads to Specialist plus Factory, which equals Enterprise">
  <defs>
    <g id="tier-card">
      <rect class="frame" x="10" y="26" width="387" height="215" rx="50"/>
      <rect class="frame-inner" x="24" y="40" width="359" height="187" rx="40"/>
      <path class="tab-fold" d="M0,50 L0,95 Q0,118 24,118 L24,60 Z"/>
      <path class="tab" d="M30,0 H230 A34,34 0 0 1 230,68 H24 Q0,68 0,88 V30 A30,30 0 0 1 30,0 Z"/>
    </g>
  </defs>

  <!-- connectors -->
  <line class="connector" x1="645" y1="501" x2="779" y2="501"/>
  <line class="connector" x1="941" y1="501" x2="1208" y2="501"/>
  <line class="connector" x1="1371" y1="501" x2="1608" y2="501"/>
  <line class="connector" x1="1770" y1="501" x2="1948" y2="501"/>
  <line class="connector" x1="1289" y1="356" x2="1289" y2="419"/>
  <line class="connector" x1="1289" y1="582" x2="1289" y2="678"/>

  <!-- Ad Hoc -->
  <g class="tier tier-adhoc" transform="translate(248,372)">
    <use href="#tier-card"/>
    <text class="tier-title" x="55" y="46">AD HOC</text>
    <text class="tier-features" x="202" y="129">Easy to Use | Reduced Errors</text>
    <text class="tier-features" x="202" y="164">Job Queue | 24 Hour Window</text>
    <circle class="dot" cx="243" cy="246" r="9"/>
  </g>

  <!-- Specialist -->
  <g class="tier tier-specialist" transform="translate(1086,114)">
    <use href="#tier-card"/>
    <text class="tier-title" x="35" y="46">SPECIALIST</text>
    <text class="tier-features" x="203" y="135">Workflow | Architecture</text>
    <text class="tier-features" x="203" y="170">Search Strategy | Case Reporting</text>
    <circle class="dot" cx="397" cy="119" r="9"/>
  </g>

  <!-- Factory -->
  <g class="tier tier-factory" transform="translate(1090,678)">
    <use href="#tier-card"/>
    <text class="tier-title" x="47" y="46">FACTORY</text>
    <text class="tier-features" x="205" y="135">Case Onboarding | Roles</text>
    <text class="tier-features" x="205" y="170">Data Re-use | Resource Mngmt</text>
    <circle class="dot" cx="58" cy="243" r="9"/>
  </g>

  <!-- Enterprise -->
  <g class="tier tier-enterprise" transform="translate(1938,374)">
    <use href="#tier-card"/>
    <text class="tier-title" x="35" y="47">ENTERPRISE</text>
    <text class="tier-features" x="203" y="131">Cross-Case Analytics | Data Lakes</text>
    <text class="tier-features" x="203" y="166">Matrixed Use | Recurring Jobs</text>
    <circle class="dot" cx="308" cy="243" r="9"/>
  </g>

  <!-- Operators -->
  <g class="operator operator-arrow">
    <circle class="operator-ring" cx="860" cy="502" r="81"/>
    <circle class="operator-disc" cx="860" cy="502" r="67"/>
    <rect class="operator-glyph" x="812" y="489" width="45" height="27"/>
    <polygon class="operator-glyph" points="852,469 909,502 852,534"/>
    <circle class="dot" cx="803" cy="562" r="9"/>
  </g>

  <g class="operator operator-plus">
    <circle class="operator-ring" cx="1289" cy="500" r="81"/>
    <circle class="operator-disc" cx="1289" cy="500" r="67"/>
    <rect class="operator-glyph" x="1276" y="455" width="26" height="91" rx="2"/>
    <rect class="operator-glyph" x="1244" y="487" width="91" height="27" rx="2"/>
    <circle class="dot" cx="1323" cy="426" r="9"/>
  </g>

  <g class="operator operator-equals">
    <circle class="operator-ring" cx="1689" cy="500" r="81"/>
    <circle class="operator-disc" cx="1689" cy="500" r="67"/>
    <rect class="operator-glyph" x="1646" y="472" width="87" height="23"/>
    <rect class="operator-glyph" x="1646" y="510" width="87" height="23"/>
    <circle class="dot" cx="1739" cy="568" r="9"/>
  </g>
</svg>
</body>
</html>
```